Tech business card design

We need an amazing business card design for our new business 'Pexla' a marketing tech startup based in Sydney, Australia. We provide an online marketplace for businesses to search and buy advertising media, connect with service providers and learn more about marketing. We wish to communicate 'cool tech', reliability and professionalism and design based around our logo.

Target Market(s)

Business Owners

Contact Information for Business Card

Name
Position
Email Address
Website
Phone Number

Font styles to use
Other font styles liked:
• Avenir & Avenir Next

Colors

Designer to choose colors to be used in the design.

```html
<!DOCTYPE html>
<html lang="en">
<head>
<meta charset="utf-8">
<title>Pexla Business Card</title>
<link href="https://fonts.googleapis.com/css2?family=Nunito+Sans:wght@400;600;800;900&display=swap" rel="stylesheet">
<style>
  :root {
    --navy: #17143f;
    --navy-soft: #2a2760;
    --white: #ffffff;
    --paper-bg: #eceeee;
    --ink: #17143f;
    --ink-muted: #5a5a6e;
    --hatch: #9a9aa8;
  }
  * { box-sizing: border-box; margin: 0; padding: 0; }
  html, body {
    width: 1200px; height: 900px; overflow: hidden;
    background: var(--paper-bg);
    font-family: "Nunito Sans", "Avenir Next", Avenir, sans-serif;
  }
  .card-sheet {
    width: 1200px; height: 900px;
    display: flex; flex-direction: column;
    align-items: center; justify-content: center; gap: 56px;
  }
  .card {
    position: relative; width: 600px; height: 367px;
    overflow: hidden; border-radius: 3px;
    box-shadow: 0 6px 18px rgba(20, 20, 50, 0.14);
  }

  /* Back side */
  .card--back { background: var(--navy); }
  .card__map {
    position: absolute; inset: 30px 40px;
    background: radial-gradient(ellipse at 50% 50%, var(--navy-soft) 0%, rgba(42,39,96,0.35) 60%, rgba(23,20,63,0) 80%);
    border-radius: 40%;
  }
  .card__brand {
    position: absolute; left: 0; right: 0; top: 140px;
    text-align: center; color: var(--white);
  }
  .card__wordmark {
    font-weight: 900; font-size: 78px; line-height: 1; letter-spacing: -2px;
  }
  .card__url {
    margin-top: 8px; font-size: 15px; font-weight: 400; letter-spacing: 0.5px;
  }

  /* Front side */
  .card--front { background: var(--white); }
  .card__tab {
    position: absolute; top: 0; right: 60px; width: 190px; height: 96px;
  }
  .card__tab-name {
    position: absolute; top: 18px; right: 60px; width: 190px;
    text-align: center; color: var(--white);
    font-weight: 900; font-size: 44px; letter-spacing: -1px; line-height: 1;
  }
  .card__stripe {
    position: absolute; right: 0; top: 0; width: 14px; height: 367px;
    display: flex; flex-direction: column;
  }
  .stripe__navy { background: var(--navy); }
  .stripe__hatch {
    background: repeating-linear-gradient(135deg, var(--hatch) 0 1px, transparent 1px 5px);
  }
  .card__bottom {
    position: absolute; left: 0; right: 0; bottom: 0; height: 14px; display: flex;
  }
  .contact {
    position: absolute; left: 48px; bottom: 62px; color: var(--ink);
  }
  .contact__name {
    font-weight: 800; font-size: 21px; letter-spacing: 0.5px; text-transform: uppercase;
  }
  .contact__role {
    font-size: 13px; color: var(--ink-muted); margin-bottom: 16px;
  }
  .contact__list { list-style: none; }
  .contact__item {
    display: flex; align-items: center; gap: 10px;
    font-size: 15px; color: var(--ink); margin-top: 5px;
  }
  .contact__icon { width: 15px; height: 15px; flex: none; }
</style>
</head>
<body>
<main class="card-sheet">

  <section class="card card--back" aria-label="Card back">
    <div class="card__map" role="img" aria-label="Faint dotted world map"></div>
    <div class="card__brand">
      <div class="card__wordmark">Pexla</div>
      <div class="card__url">www.pexlamedia.com.au</div>
    </div>
  </section>

  <section class="card card--front" aria-label="Card front">
    <svg class="card__tab" viewBox="0 0 190 96" aria-hidden="true">
      <path d="M0 0 H190 V72 Q190 96 166 96 H36 L0 60 Z" fill="var(--navy)"/>
    </svg>
    <div class="card__tab-name">Pexla</div>

    <div class="card__stripe">
      <div class="stripe__navy" style="height:150px"></div>
      <div class="stripe__hatch" style="height:120px"></div>
      <div class="stripe__navy" style="flex:1"></div>
    </div>

    <div class="card__bottom">
      <div class="stripe__navy" style="width:60px"></div>
      <div class="stripe__hatch" style="width:200px"></div>
      <div class="stripe__navy" style="flex:1"></div>
    </div>

    <div class="contact">
      <div class="contact__name">Mark Dalton</div>
      <div class="contact__role">Founder | Director</div>
      <ul class="contact__list">
        <li class="contact__item">
          <svg class="contact__icon" viewBox="0 0 16 16" aria-hidden="true"><rect x="4" y="1" width="8" height="14" rx="1.5" fill="none" stroke="var(--ink)" stroke-width="1.4"/><circle cx="8" cy="12.5" r="0.9" fill="var(--ink)"/></svg>
          +61 (0)400 555 012
        </li>
        <li class="contact__item">
          <svg class="contact__icon" viewBox="0 0 16 16" aria-hidden="true"><rect x="1" y="3" width="14" height="10" rx="1" fill="var(--ink)"/><path d="M1.5 3.8 L8 9 L14.5 3.8" fill="none" stroke="var(--white)" stroke-width="1.2"/></svg>
          mark@pexlamedia.com.au
        </li>
        <li class="contact__item">
          <svg class="contact__icon" viewBox="0 0 16 16" aria-hidden="true"><circle cx="8" cy="8" r="7" fill="var(--ink)"/><ellipse cx="8" cy="8" rx="3" ry="7" fill="none" stroke="var(--white)" stroke-width="1"/><path d="M1 8 H15" stroke="var(--white)" stroke-width="1"/></svg>
          www.pexlamedia.com.au
        </li>
      </ul>
    </div>
  </section>

</main>
</body>
</html>
```